Large online photo magazine needs redesign

We have previously digitised a historical photographic magazine of around 20,000 printed pages and made it available online. The magazine ran up to the early 1970s, and the content is largely black and white photographs of local events, accompanied by short captions.

Although the content is very rich, the design needs to be revisited so that:
* it is visually appealing
* it is responsive (i.e. works in browsers across all manner of devices)
* is faithful to the nature of the content

There are only a few core page types, and the central one is the article page, an example of which can be seen at:
http://snapgazette.example/gisborne/issue/KLR48_19600714/t1-body-d4.html

Any design submitted should be based on the treatment of an article page such as the above.

Given the large number of pages on our site, we need a design which can be templated to work for any content in the collection, i.e. we cannot hand-craft our templates to match a given page of content, rather a template must work acceptably well for all content.

The current site, although basic in design, has the advantage that it is quite efficient in the amount of data per page request (around 100k - 200k). While not adverse to web fonts, banner imagery etc, we will carefully consider the benefit gained from any such treatment against the amount of extra data that needs to be downloaded to the client's browser.

For the right design, we are able ourselves to adapt it to a CSS layout.

An example of each core page type is as follows (though for this project we only expect a design for a single page, as itemised above):

http://snapgazette.example/gisborne/index.html
http://snapgazette.example/gisborne/about.html
http://snapgazette.example/gisborne/help.html
http://snapgazette.example/gisborne/initial/index.html
http://snapgazette.example/gisborne/search/results?type=section&text=smith&cmdSubmit=Go
http://snapgazette.example/gisborne/advanced-search/index.html
http://snapgazette.example/gisborne/issue/KLR48_19600714/t1-front-d1.html
http://snapgazette.example/gisborne/issue/KLR48_19600714/index.html
http://snapgazette.example/gisborne/issue/KLR48_19600714/fig-KLR48_19600714_005a.html
http://snapgazette.example/gisborne/issue/KLR48_19600714/KLR48_19600714_012.html
http://snapgazette.example/gisborne/issue/KLR48_19600714/thumbnails.html

Target Market(s)

A general browsing audience of all ages, but skewed towards the older generations, and those interested in family / regional history.

The average user will not be particularly web-savy, and the treatment of the content should not detract / distract from the actual content itself.

Industry/Entity Type

Events

Requirements
Must have
• * it is visually appealing
The content should be visually appealing to the audience, which can be defined as a general browsing audience of all ages, but skewed towards the middle and older generations.

* it is responsive (the design can be adapted - by us - to work in browsers across all manner of devices)

The magazine covers (http://snapgazette.example/gisborne/issues/index.html) offer some possible inspiration for treatment of the material.

```html
<!DOCTYPE html>
<html lang="en">
<head>
<meta charset="utf-8">
<title>Snap Gazette – Engaged</title>
<link rel="stylesheet" href="https://fonts.googleapis.com/css2?family=Source+Sans+3:ital,wght@0,400;0,600;0,700;1,400&display=swap">
<style>
:root{
  --brand:#c63b4e;
  --brand-dark:#a3283a;
  --brand-deep:#8e1f30;
  --ink:#333;
  --muted:#555;
  --rule:#dcdcdc;
  --btn:#3f3f3f;
  --footer:#262626;
  --footer-deep:#1b1b1b;
  --sepia-a:#cfc3a0;
  --sepia-b:#8c8470;
}
*{box-sizing:border-box;margin:0;padding:0}
html,body{width:821px;height:1200px;overflow:hidden}
body{position:relative;background:#fff;font-family:"Source Sans 3",Arial,sans-serif;color:var(--ink)}
.abs{position:absolute}
.site-header{position:absolute;left:0;top:0;width:821px;height:92px;background:var(--brand)}
.header-band{position:absolute;left:0;top:92px;width:821px;height:31px;background:var(--brand-dark)}
.brand{position:absolute;left:48px;top:22px;color:#fff;font-weight:700;font-size:36px;letter-spacing:.5px;line-height:1}
.search{position:absolute;left:577px;top:38px;width:184px;height:36px;background:var(--brand-deep);padding:6px}
.search-field{width:100%;height:100%;background:#fff;border-radius:2px;font-size:9.5px;color:#444;padding:0 10px;display:flex;align-items:center;justify-content:space-between}
.main-nav{position:absolute;left:59px;top:86px;width:703px;height:41px;background:#fff;border-bottom:3px solid #cfcfcf;display:flex;align-items:stretch}
.main-nav a{display:flex;align-items:center;padding:0 9px;font-size:10px;color:var(--brand);text-decoration:none;border-right:1px solid #e4e4e4}
.main-nav a.active{background:#474747;color:#fff;padding:0 17px}
.social{margin-left:auto;display:flex;gap:7px;align-items:center;padding-right:15px}
.social span{width:16px;height:16px;border-radius:3px;display:block}
.section-title{font-size:17px;font-weight:700;color:#333}
.card{position:absolute;top:182px;width:226px;height:234px;border:1px solid var(--rule);background:repeating-linear-gradient(45deg,#fafafa 0 3px,#f2f2f2 3px 4px)}
.photo{background:linear-gradient(135deg,var(--sepia-a),var(--sepia-b))}
.card .photo{position:absolute;left:7px;top:7px;width:211px;height:141px}
.card p{position:absolute;left:7px;top:157px;width:211px;font-size:9.6px;line-height:13px;font-style:italic;color:#444}
.btn-more{position:absolute;right:8px;bottom:7px;background:var(--btn);color:#fff;font-size:9px;padding:4px 5px;border-radius:2px}
.arrow{position:absolute;top:272px;width:24px;height:24px;border-radius:50%;background:#3b3b3b}
.post-meta{font-size:10px;color:#555}
.post-meta b{color:#222;font-weight:600}
.comments{position:absolute;left:436px;top:469px;width:87px;height:27px;background:#4b4b4b;border-radius:2px;color:#eee;font-size:9.5px;font-style:italic;display:flex;align-items:center;justify-content:center}
.post-frame{position:absolute;left:59px;top:513px;width:464px;height:223px;border:1px solid var(--rule);background:#f5f5f5}
.post-frame .photo{position:absolute;left:12px;top:11px;width:439px;height:199px}
.post-caption{position:absolute;left:60px;top:747px;width:460px;font-size:10.3px;line-height:16.5px;font-style:italic;color:#444}
.read-more{position:absolute;left:458px;top:808px;font-size:10px;color:#222;display:flex;align-items:center;gap:3px}
.divider{position:absolute;left:59px;top:837px;width:464px;height:5px;background:repeating-linear-gradient(45deg,#ddd 0 1px,#fff 1px 3px)}
.older{position:absolute;left:57px;top:860px;width:119px;height:34px;background:var(--btn);color:#fff;font-size:14px;display:flex;align-items:center;gap:10px;padding-left:12px;border-bottom:2px solid #222}
.widget{position:absolute;left:554px;width:207px;border:1px solid var(--rule);padding:0 13px}
.widget h3{font-size:13.5px;font-weight:400;color:var(--brand);margin-top:7px}
.tweet{font-size:9.6px;line-height:13.5px;font-style:italic;color:#333;margin-top:12px}
.tweet-time{font-size:9.6px;font-weight:700;margin-top:5px}
.email{height:23px;border:1px solid #ccc;font-size:9.5px;padding:0 8px;display:flex;align-items:center;margin-top:10px}
.send{margin:8px 0 0 auto;width:55px;height:20px;background:var(--brand-dark);color:#fff;font-size:10px;display:flex;align-items:center;justify-content:center}
.site-footer{position:absolute;left:0;top:921px;width:821px;height:234px;background:var(--footer)}
.footer-bar{position:absolute;left:0;top:1155px;width:821px;height:45px;background:var(--footer-deep);color:#ccc;font-size:8px;text-align:center;line-height:45px}
.fcol{position:absolute;top:950px;color:#eee}
.fcol h4{font-size:16px;font-weight:400;margin-bottom:9px}
.fcol p{font-size:9.3px;line-height:15px;color:#ddd;margin-bottom:8px;width:200px}
.fcol ul{list-style:none;width:134px}
.fcol li{font-size:9px;height:19.4px;line-height:19px;border-bottom:1px solid #444;color:#eee;padding-left:13px;position:relative}
.fcol li::before{content:"";position:absolute;left:1px;top:7px;width:4px;height:4px;border-right:1.5px solid #fff;border-top:1.5px solid #fff;transform:rotate(45deg)}
</style>
</head>
<body>
<header class="site-header">
  <div class="brand">Snap Gazette</div>
  <div class="search"><div class="search-field">Search Snap Gazette
    <svg width="12" height="12" viewBox="0 0 12 12"><circle cx="7" cy="5" r="3.5" fill="none" stroke="#888" stroke-width="1.3"/><line x1="4.5" y1="7.5" x2="1" y2="11" stroke="#888" stroke-width="1.6"/></svg></div></div>
</header>
<div class="header-band"></div>
<nav class="main-nav">
  <a class="active">Home</a><a>About</a><a>Browse Snap Gazette</a><a>A-Z people</a><a>Advanced search</a><a>Help</a><a>Report an error</a><a style="border:none">Contact</a>
  <div class="social"><span style="background:#f0962a"></span><span style="background:#5fb9e0"></span><span style="background:#3b5b9a"></span></div>
</nav>

<h2 class="section-title abs" style="left:64px;top:146px">Flying Sisters from Gisborne</h2>
<div class="arrow" style="left:32px"><svg width="24" height="24"><polyline points="14,8 10,12 14,16" fill="none" stroke="#fff" stroke-width="2"/></svg></div>
<div class="arrow" style="left:766px"><svg width="24" height="24"><polyline points="10,8 14,12 10,16" fill="none" stroke="#fff" stroke-width="2"/></svg></div>
<article class="card" style="left:59px">
  <div class="photo" role="img" aria-label="Black and white photo of three sisters in air hostess uniforms"></div>
  <p>This is probably something of a record--three sisters who are all air hostesses. They are the Harlow sisters.....</p>
  <span class="btn-more">Read More</span>
</article>
<article class="card" style="left:297px">
  <div class="photo" role="img" aria-label="Black and white photo of a young air hostess seated by an aircraft window"></div>
  <p>And this young lady, Muriel Dawlish, of Auckland, has made history in another way. She was the first air hostess to make....</p>
  <span class="btn-more">Read More</span>
</article>
<article class="card" style="left:536px">
  <div class="photo" role="img" aria-label="Magazine clipping of an old truss bridge across a river"></div>
  <p>The old highway bridge across the Waiapu River near Ruatoria probably has more Bailey "splints" than any other bridge in the country...</p>
  <span class="btn-more">Read More</span>
</article>

<h2 class="section-title abs" style="left:60px;top:451px">Engaged</h2>
<div class="post-meta abs" style="left:61px;top:485px"><b>No 73</b> &nbsp;<span style="color:#bbb">|</span>&nbsp; July 14, 1960</div>
<div class="comments">14 Comments</div>
<div class="post-frame"><div class="photo" role="img" aria-label="Scanned magazine spread with engagement portraits, air hostesses and a bridge"></div></div>
<p class="post-caption">The old highway bridge across the Waiapu River near Ruatoria probably has more Bailey "splints" than any other bridge in the country. It is to be replaced soon by a modern structure two miles downstream, after which all main-route traffic will pass through Ruatoria township. (Picture, Eastland).</p>
<div class="read-more"><svg width="10" height="10"><circle cx="5" cy="5" r="5" fill="#222"/><path d="M5 2.5v5M2.5 5h5" stroke="#fff" stroke-width="1.3"/></svg>Read More</div>
<div class="divider"></div>
<div class="older"><svg width="8" height="10"><polyline points="6,1 2,5 6,9" fill="none" stroke="#fff" stroke-width="2"/></svg>Older Posts</div>

<aside class="widget" style="top:466px;height:285px">
  <h3>Latest from Chirper</h3>
  <span class="abs" style="left:172px;top:-4px;width:28px;height:28px;border-radius:50%;background:#4aa8d8"></span>
  <p class="tweet" style="margin-top:14px">This is probably something of a record--three sisters who are all air hostesses. They are the Harlow</p><p class="tweet-time">2-days ago</p>
  <p class="tweet" style="margin-top:19px">This is probably something of a record--three sisters who are all air hostesses. They are the Harlow</p><p class="tweet-time">4-days ago</p>
  <p class="tweet" style="margin-top:19px">This is probably something of a record--three sisters who are all air hostesses. They are the Harlow</p><p class="tweet-time">4-days ago</p>
</aside>
<aside class="widget" style="top:772px;height:95px">
  <h3 style="margin-top:8px">Subscribe to Our Newsletter</h3>
  <div class="email">Email Adress</div>
  <div class="send">Send</div>
</aside>

<footer class="site-footer"></footer>
<div class="fcol" style="left:57px">
  <h4>Footer Text Widget</h4>
  <p>The old highway bridge across the Waiapu River near Ruatoria probably has more Bailey "splints" than any other bridge in the country. It is to be replaced soon by a modern</p>
  <p>The old highway bridge across the Waiapu River near Ruatoria probably has more Bailey "splints" than any other bridge in the country. It is to be replaced soon by a modern</p>
</div>
<div class="fcol" style="left:287px;top:947px">
  <h4>Quick Links</h4>
  <ul><li>Home</li><li>About</li><li>Browse Snap Gazette</li><li>A-Z people</li><li>Advanced search</li><li>Help</li><li>Report an error</li><li>Contact</li></ul>
</div>
<div class="fcol" style="left:455px;top:947px">
  <h4>Pages</h4>
  <ul><li>Article new 1</li><li>Article new 1</li><li>Browse Snap Gazette</li><li>A-Z people</li><li>Article new 2</li><li>Help</li><li>Article new 3</li><li>Article new 5</li></ul>
</div>
<div class="fcol" style="left:622px;top:947px">
  <h4>Categories</h4>
  <ul><li>Friendbook</li><li>Chirper</li><li>Linkwork</li><li>Categories1</li><li>Video Archives</li><li>Categories1</li><li>Categories1</li><li>Categories1</li></ul>
</div>
<div class="footer-bar">© 2014 Eastbay Heritage Library All Rights Reserved</div>
</body>
</html>
```